Business Card for a Dental Office

The design should communicate integrity, quality and reliability. We also want the card look elegant, simple, but still stand out, different from the traditional-dental-office business card.

Industry/Entity Type

Business

```html
<!DOCTYPE html>
<html lang="en">
<head>
<meta charset="utf-8">
<title>Harlow Dental Studio – Business Card</title>
<link href="https://fonts.googleapis.com/css2?family=Source+Sans+3:wght@400;600;700&display=swap" rel="stylesheet">
<style>
  :root {
    --page: #dcdcda;
    --card: #f6f6f4;
    --ink: #1c1c1c;
    --ink-soft: #2e2e2e;
    --gold: #b08d12;
    --gold-deep: #8c6e14;
    --gold-light: #eee05a;
    --gold-mid: #d4bb10;
    --band-dark: #141414;
    --white: #ffffff;
  }
  * { margin: 0; padding: 0; box-sizing: border-box; }
  html, body {
    width: 1200px; height: 970px; overflow: hidden;
    background: var(--page);
    font-family: "Source Sans 3", Arial, sans-serif;
    color: var(--ink);
  }
  .card {
    position: absolute; left: 100px; top: 207px;
    width: 1000px; height: 556px;
    background: var(--card);
    box-shadow: 0 6px 24px rgba(0,0,0,0.12);
    overflow: hidden;
  }
  .brand { position: absolute; left: 48px; top: 96px; display: flex; align-items: center; gap: 22px; }
  .brand-mark { width: 92px; height: 92px; background: var(--gold); flex: none; }
  .brand-text { display: flex; flex-direction: column; }
  .brand-name {
    font-weight: 700; font-size: 46px; line-height: 1; letter-spacing: 1px;
    text-transform: uppercase; color: var(--ink);
  }
  .brand-tagline {
    margin-top: 8px; font-weight: 600; font-size: 21px; letter-spacing: 1.2px;
    text-transform: uppercase; color: var(--gold-deep);
  }
  .person { position: absolute; right: 131px; top: 285px; text-align: right; }
  .person-name { font-weight: 600; font-size: 28px; line-height: 1.1; color: var(--ink); }
  .person-role { font-size: 22px; line-height: 1.2; color: var(--ink); }
  .accent-bar {
    position: absolute; left: 981px; top: 288px; width: 19px; height: 56px;
    background: linear-gradient(180deg, var(--gold-mid), var(--gold-deep));
  }
  .rule { position: absolute; left: 48px; top: 339px; width: 783px; height: 2px; background: var(--ink); }
  .address { position: absolute; left: 48px; top: 418px; font-size: 22px; line-height: 32px; color: var(--ink-soft); }
  .contacts { position: absolute; right: 40px; top: 386px; list-style: none; }
  .contacts li {
    display: flex; justify-content: flex-end; align-items: center; gap: 14px;
    font-size: 22px; line-height: 32px; color: var(--ink);
  }
  .contacts svg { width: 22px; height: 18px; fill: var(--gold); flex: none; }
  .band {
    position: absolute; left: 0; bottom: 0; width: 100%; height: 43px;
    background: linear-gradient(90deg, var(--band-dark) 0%, var(--band-dark) 52%, var(--gold-mid) 58%, var(--gold-light) 80%, var(--gold-mid) 100%);
    display: flex; align-items: center; justify-content: center;
  }
  .band-name {
    font-weight: 600; font-size: 15px; letter-spacing: 1px; text-transform: uppercase;
    color: var(--white); padding-left: 8px;
  }
</style>
</head>
<body>
  <div class="card">
    <div class="brand">
      <div class="brand-mark"></div>
      <div class="brand-text">
        <span class="brand-name">Harlow Dental Studio</span>
        <span class="brand-tagline">Your smile is your gift to others</span>
      </div>
    </div>

    <div class="person">
      <p class="person-name">Elliot Crane, PHA</p>
      <p class="person-role">President</p>
    </div>
    <div class="accent-bar"></div>
    <div class="rule"></div>

    <address class="address" style="font-style:normal">
      Level 12, 48 Meridian House<br>
      Sydney, New South Wales
    </address>

    <ul class="contacts">
      <li>+ 000 000 0000
        <svg viewBox="0 0 22 18" aria-hidden="true"><path d="M2 6c0-3 4-5 9-5s9 2 9 5v2h-5V6c-1-1-3-1-4-1s-3 0-4 1v2H2z"/><rect x="4" y="9" width="14" height="8" rx="1"/></svg>
      </li>
      <li>+ 000 000 0000
        <svg viewBox="0 0 22 18" aria-hidden="true"><rect x="6" y="1" width="10" height="5"/><rect x="1" y="6" width="20" height="8" rx="1"/><rect x="6" y="11" width="10" height="6" fill="#f6f6f4"/><rect x="7" y="12" width="8" height="5"/></svg>
      </li>
      <li>info@harlowdentalstudio.com
        <svg viewBox="0 0 22 18" aria-hidden="true"><path d="M1 3h20v12H1z"/><path d="M1 3l10 7 10-7" fill="none" stroke="#f6f6f4" stroke-width="1.5"/></svg>
      </li>
    </ul>

    <div class="band">
      <span class="band-name">Harlow Dental Studio</span>
    </div>
  </div>
</body>
</html>
```